Business Card Design for Property Development Company Director

I am looking for a professional and unforgettable business card design for our Director of our Property Development Company.
Please see attached .pptx file to find out what information to include. You don't have to follow the exact format shown in the file - I am interested to see your creative flair using the information provided.

```html
<!DOCTYPE html>
<html lang="en">
<head>
<meta charset="utf-8">
<title>Calverly Property Group – Business Card</title>
<link href="https://fonts.googleapis.com/css2?family=Roboto:wght@400;500;700&family=Roboto+Condensed:wght@700&display=swap" rel="stylesheet">
<style>
  :root {
    --backdrop: #e4e5e7;
    --card: #fbfbfb;
    --brand-blue: #27479a;
    --brand-grey: #55575b;
    --text-grey: #5f6166;
    --rule: #d3d4d6;
  }
  * { box-sizing: border-box; margin: 0; padding: 0; }
  html, body { width: 1200px; height: 726px; overflow: hidden; }
  body {
    background: var(--backdrop);
    font-family: "Roboto", Arial, sans-serif;
    position: relative;
  }
  .card {
    position: absolute;
    top: 213px;
    width: 540px;
    height: 300px;
    background: var(--card);
    box-shadow: 0 6px 18px rgba(0,0,0,0.12);
    overflow: hidden;
  }
  .card--front { left: 40px; }
  .card--back { left: 620px; }

  .edge-band {
    position: absolute;
    left: 0; right: 0; bottom: 0;
    height: 12px;
    display: flex;
  }
  .edge-band__grey { background: var(--brand-grey); width: 46%; }
  .edge-band__blue { background: var(--brand-blue); flex: 1; }

  .wordmark {
    display: flex;
    align-items: center;
    gap: 12px;
  }
  .wordmark__square {
    width: 34px; height: 34px;
    background: var(--brand-blue);
    flex: none;
  }
  .wordmark__name {
    font-weight: 700;
    color: var(--brand-grey);
    letter-spacing: 1px;
    line-height: 1.05;
    text-transform: uppercase;
  }

  /* front */
  .front__tagline {
    position: absolute;
    top: 38px; left: 0; right: 0;
    text-align: center;
    color: var(--brand-blue);
    font-size: 19px;
    line-height: 1.25;
  }
  .front__wordmark {
    position: absolute;
    top: 118px; left: 0; right: 0;
    justify-content: center;
  }
  .front__wordmark .wordmark__square { width: 48px; height: 48px; }
  .front__wordmark .wordmark__name { font-size: 30px; }
  .front__invite {
    position: absolute;
    top: 222px; left: 0; right: 0;
    text-align: center;
    font-size: 15px;
    color: var(--text-grey);
  }
  .front__invite strong { color: var(--brand-blue); font-weight: 400; }

  /* back */
  .back__wordmark {
    position: absolute;
    top: 40px; left: 44px;
  }
  .back__wordmark .wordmark__name { font-size: 24px; }
  .back__person {
    position: absolute;
    top: 170px; left: 44px;
  }
  .back__name {
    font-family: "Roboto Condensed", Arial, sans-serif;
    font-weight: 700;
    font-size: 22px;
    color: var(--brand-blue);
  }
  .back__role {
    font-size: 14px;
    color: var(--text-grey);
    text-align: right;
    margin-top: 2px;
  }
  .back__contacts {
    position: absolute;
    top: 112px; left: 270px;
    list-style: none;
    font-size: 14px;
    color: var(--text-grey);
  }
  .back__contacts li {
    display: flex;
    align-items: center;
    gap: 10px;
    height: 22px;
  }
  .back__contacts svg { width: 13px; height: 13px; fill: var(--brand-grey); flex: none; }
  .back__rule {
    position: absolute;
    left: 44px; right: 36px; top: 232px;
    height: 1px;
    background: var(--rule);
  }
  .back__licence {
    position: absolute;
    top: 244px; left: 0; right: 0;
    text-align: center;
    font-size: 14px;
    color: var(--text-grey);
  }
  .back__licence span { color: var(--brand-blue); }
</style>
</head>
<body>

<section class="card card--front">
  <p class="front__tagline">Property Development<br>&amp; Site Acquisition Specialists</p>
  <div class="wordmark front__wordmark">
    <span class="wordmark__square"></span>
    <span class="wordmark__name">Calverly<br>Property Group</span>
  </div>
  <p class="front__invite">Ask me about our <strong>INVESTMENT &amp; PARTNERSHIP</strong> opportunities</p>
  <div class="edge-band"><span class="edge-band__grey"></span><span class="edge-band__blue"></span></div>
</section>

<section class="card card--back">
  <div class="wordmark back__wordmark">
    <span class="wordmark__square"></span>
    <span class="wordmark__name">Calverly<br>Property Group</span>
  </div>

  <ul class="back__contacts">
    <li>
      <svg viewBox="0 0 24 24" aria-hidden="true"><path d="M6.6 10.8a15.1 15.1 0 0 0 6.6 6.6l2.2-2.2a1 1 0 0 1 1-.25 11.4 11.4 0 0 0 3.6.57 1 1 0 0 1 1 1V20a1 1 0 0 1-1 1A17 17 0 0 1 3 4a1 1 0 0 1 1-1h3.5a1 1 0 0 1 1 1c0 1.25.2 2.45.57 3.6a1 1 0 0 1-.25 1z"/></svg>
      0400 123 456
    </li>
    <li>
      <svg viewBox="0 0 24 24" aria-hidden="true"><path d="M2 5h20v14H2z M2 5l10 8 10-8" fill="none" stroke="#55575b" stroke-width="2"/></svg>
      daniel@calverly.com.au
    </li>
    <li>
      <svg viewBox="0 0 24 24" aria-hidden="true"><circle cx="12" cy="12" r="9" fill="none" stroke="#55575b" stroke-width="2"/><path d="M3 12h18M12 3c3 3 3 15 0 18M12 3c-3 3-3 15 0 18" fill="none" stroke="#55575b" stroke-width="1.6"/></svg>
      www.calverly.com.au
    </li>
  </ul>

  <div class="back__person">
    <p class="back__name">Daniel Marsh</p>
    <p class="back__role">Director</p>
  </div>

  <div class="back__rule"></div>
  <p class="back__licence">Real Estate Lic: <span>5120394 &amp; 5120395</span></p>
  <div class="edge-band"><span class="edge-band__grey"></span><span class="edge-band__blue"></span></div>
</section>

</body>
</html>
```